Business Card - connecting 2 souls and beggining the journey of self discovery

Logo on the front
with tag line

On the back list of services and contact details

Seminars
workshops
Coaching
podcasts

Darren Whitlow
Health & Wellbeing Life Coach
0491 372 615
darren@brightcoreliving.example
brightcoreliving.example

Industry/Entity Type

Life Coaching

Contact Information for Business Card

I like the use of colour from the logo to be used. I'm not a fan of white.

Requirements
Must have
• My tagline: The journey home starts with you
Nice to have
• Use of colour that is in the Brightcore logo

```html
<!DOCTYPE html>
<html lang="en">
<head>
<meta charset="utf-8">
<title>Brightcore Living – Business Card</title>
<link rel="stylesheet" href="https://fonts.googleapis.com/css2?family=Open+Sans:wght@400;600&family=Montserrat:wght@500;600&display=swap">
<style>
  :root {
    --stage: #242424;
    --card-light: #f2f2f2;
    --ink: #1f1f1f;
    --coral: #ee5b5b;
    --warm-coral: #ef7d6a;
    --sun: #f6d54a;
    --amber: #f4b23c;
    --orange: #f48a4a;
    --lime: #d9d84a;
    --white: #ffffff;
  }
  * { margin: 0; padding: 0; box-sizing: border-box; }
  html, body {
    width: 1200px; height: 900px; overflow: hidden;
    background: var(--stage);
    font-family: "Open Sans", Arial, sans-serif;
  }
  .canvas { position: relative; width: 1200px; height: 900px; }

  .card {
    position: absolute; top: 170px;
    width: 347px; height: 561px; overflow: hidden;
  }

  /* Contact side */
  .card--contact { left: 259px; background: var(--card-light); text-align: center; color: var(--ink); }
  .brand-mark {
    position: absolute; left: 0; right: 0; top: 76px;
    display: flex; flex-direction: column; align-items: center; gap: 16px;
  }
  .brand-mark__dot {
    width: 96px; height: 96px; border-radius: 50%;
    background: var(--coral);
  }
  .brand-mark__name {
    font-size: 26px; font-weight: 600; color: var(--coral); letter-spacing: 0.5px;
  }
  .person { position: absolute; left: 0; right: 0; top: 320px; }
  .person__name {
    font-size: 20px; font-weight: 600; color: var(--coral);
    text-transform: uppercase; line-height: 26px; letter-spacing: 0.3px;
  }
  .person__role { font-size: 14.5px; line-height: 18px; }
  .contact { position: absolute; left: 0; right: 0; top: 383px; font-size: 14.5px; line-height: 20.5px; }
  .contact__label { color: var(--coral); font-weight: 600; }
  .contact__web { color: var(--coral); font-weight: 600; }

  .services {
    position: absolute; top: 473px; left: 58px;
    display: grid; grid-template-columns: 131px 110px; row-gap: 3px;
    list-style: none; font-size: 19px; line-height: 22px; text-align: left;
  }
  .services li { display: flex; align-items: center; gap: 6px; }
  .services li::before {
    content: ""; width: 12px; height: 12px; border-radius: 50%;
    background: var(--coral); flex: none;
  }

  /* Brand side */
  .card--brand {
    left: 631px; color: var(--white); text-align: center;
    background:
      radial-gradient(circle at 250px 150px, rgba(246,214,74,0.9) 0 90px, rgba(246,214,74,0) 160px),
      radial-gradient(circle at 100px 330px, rgba(220,216,74,0.85) 0 100px, rgba(220,216,74,0) 180px),
      radial-gradient(circle at 260px 390px, rgba(246,190,60,0.8) 0 90px, rgba(246,190,60,0) 170px),
      radial-gradient(circle at 140px 50px, rgba(244,150,80,0.8) 0 60px, rgba(244,150,80,0) 140px),
      linear-gradient(160deg, var(--warm-coral) 0%, var(--amber) 45%, var(--lime) 70%, var(--orange) 100%);
  }
  .brand-badge {
    position: absolute; left: 50%; top: 202px; transform: translateX(-50%);
    display: flex; flex-direction: column; align-items: center; gap: 8px;
  }
  .brand-badge__dot { width: 56px; height: 56px; border-radius: 50%; background: var(--coral); }
  .brand-badge__name { font-size: 17px; font-weight: 600; color: var(--white); }
  .headline {
    position: absolute; left: 0; right: 0; top: 332px;
    font-family: "Montserrat", Arial, sans-serif; font-weight: 500;
    font-size: 24px; letter-spacing: -0.6px;
  }
  .tagline {
    position: absolute; left: 0; right: 0; top: 388px;
    font-size: 14px; font-weight: 600; text-transform: uppercase; letter-spacing: 0.2px;
  }
</style>
</head>
<body>
<main class="canvas">
  <section class="card card--contact">
    <div class="brand-mark">
      <span class="brand-mark__dot"></span>
      <span class="brand-mark__name">Brightcore</span>
    </div>
    <div class="person">
      <h1 class="person__name">Darren Whitlow</h1>
      <p class="person__role">Health &amp; Wellbeing Life Coach</p>
    </div>
    <div class="contact">
      <p><span class="contact__label">P:</span> 0491 372 615</p>
      <p><span class="contact__label">E:</span> darren@brightcoreliving.example</p>
      <p class="contact__web">www.brightcoreliving.example</p>
    </div>
    <ul class="services">
      <li>Seminars</li>
      <li>Coaching</li>
      <li>Workshops</li>
      <li>Podcasts</li>
    </ul>
  </section>

  <section class="card card--brand">
    <div class="brand-badge">
      <span class="brand-badge__dot"></span>
      <span class="brand-badge__name">Brightcore</span>
    </div>
    <h2 class="headline">Home of Brightcore Living</h2>
    <p class="tagline">The journey home starts with you</p>
  </section>
</main>
</body>
</html>
```